Short fill E liquid label UK. 100ml Nicotine free

Short Fill e liquid label (UK). The BRAND name is "Lumora" (Logo uploaded).Looking to release a new range under the Lumora name. The new range will be called "Glitch". A range of Liquids mixed together. Needs to look cool, stand out and funky but not too crazy. The range will have 10 different flavours so will need these all done, a simple flavour name towards bottom of label will do for this or a different colour for each.Any warnings ( requirements by law) etc and company address/details etc need to have a place on the labels. Basically need to be E liquid compliant label but all are nicotine free so not so many law requirements.Label Size will be 120mm( wide)x 60mm(high), bottle diameter is 41mm .

The 10 flavour names are as follows so will need appropriate colours for each flavour:
Berserker ( a menthol and custard mix )
Fruit loop ( a mixed fruit mix )
Smooth custard ( custard based mix )
Strawberry Shake ( Strawberry milkshake mix )
Cookie Jar ( a cookie based mix )
Black ice ( a liquorice and menthol mix )
Madagascan breeze ( Mainly vanilla based mix )
Choc shake ( chocolate milkshake )
nutter ( a peanut butter and banana mix )
Cool currant ( blackcurrant and menthol mix )

Requirements
Must have
• The info and warnings that need to be on the bottle are as follows:
• signs that need to be on bottle:
• 18+ sign
• Caution sign (!)
• United kingdom flag with" made in the united kingdom written underneath"
• text that needs to be on the bottle:
• Nicotine free eliquid. (in bold lettering )
• Keep out of the reach of children. Always
• read the label before use.
• If swallowed consult a doctor if feeling unwell . In case of contact with eyes consult a doctor.
• Dispose of in a responsible manner.
• Store in a dark place at room temperature.
• Ingredients:
• Vegetable glycerin, Propylene glycol, Flavourings.
• PG/VG ratio 70/30 %

```html
<!DOCTYPE html>
<html lang="en">
<head>
<meta charset="utf-8">
<title>Lumora Glitch – Shortfill Label</title>
<link rel="stylesheet" href="https://fonts.googleapis.com/css2?family=Lato:wght@400;700;900&display=swap">
<style>
  :root {
    --page: #ffffff;
    --label-dark: #141414;
    --label-mid: #1f1f1f;
    --ink: #ffffff;
    --ink-soft: #e8e8e8;
    --box: #ffffff;
    --box-ink: #1a1a1a;
    --flag-blue: #012169;
    --flag-red: #c8102e;
  }
  * { margin: 0; padding: 0; box-sizing: border-box; }
  html, body {
    width: 884px; height: 1200px; overflow: hidden;
    background: var(--page);
    font-family: "Lato", sans-serif;
  }
  .canvas { position: relative; width: 884px; height: 1200px; }
  .label {
    position: absolute; left: 45px; top: 401px;
    width: 794px; height: 398px;
    background: linear-gradient(135deg, var(--label-mid) 0%, var(--label-dark) 45%, var(--label-mid) 100%);
    color: var(--ink);
  }
  .col { position: absolute; top: 0; text-align: center; height: 100%; }
  .col-left { left: 38px; width: 190px; }
  .col-centre { left: 264px; width: 260px; }
  .col-right { left: 562px; width: 200px; }
  .heading { font-weight: 700; font-size: 15px; }
  .body-text { font-size: 11px; line-height: 14.5px; color: var(--ink-soft); }
  .warnings-heading { position: absolute; top: 40px; left: 0; width: 100%; }
  .warnings-text { position: absolute; top: 66px; left: 0; width: 100%; }
  .signs { position: absolute; top: 216px; left: 0; width: 100%; display: flex; justify-content: center; gap: 6px; }
  .sign {
    width: 54px; height: 54px; border-radius: 50%;
    background: var(--box); color: var(--box-ink);
    display: flex; align-items: center; justify-content: center;
    font-weight: 900; font-size: 17px;
  }
  .address-heading { position: absolute; top: 284px; left: 0; width: 100%; }
  .address-text { position: absolute; top: 308px; left: 0; width: 100%; }

  .brand-mark {
    position: absolute; top: 40px; left: 68px;
    width: 124px; height: 124px; border-radius: 50%;
    border: 3px solid var(--ink);
    display: flex; align-items: center; justify-content: center;
    font-weight: 700; font-size: 26px;
  }
  .range-name {
    position: absolute; top: 196px; left: 0; width: 100%;
    font-weight: 900; font-size: 64px; line-height: 1; text-transform: uppercase; letter-spacing: 1px;
  }
  .product-type {
    position: absolute; top: 298px; left: 0; width: 100%;
    font-weight: 900; font-size: 12px; letter-spacing: 3px; text-transform: uppercase;
  }
  .spec {
    position: absolute; top: 343px; left: 74px; width: 121px; height: 28px;
    border-left: 2px solid var(--ink); border-right: 2px solid var(--ink);
    font-weight: 700; font-size: 11px; line-height: 13px;
  }
  .spec::before, .spec::after {
    content: ""; position: absolute; left: 0; width: 8px; height: 2px; background: var(--ink);
  }
  .spec::before { top: 0; }
  .spec::after { bottom: 0; }
  .spec-inner { position: absolute; inset: 0; }
  .spec-inner::before, .spec-inner::after {
    content: ""; position: absolute; right: 0; width: 8px; height: 2px; background: var(--ink);
  }
  .spec-inner::before { top: 0; }
  .spec-inner::after { bottom: 0; }

  .ingredients-heading { position: absolute; top: 44px; left: 0; width: 100%; }
  .ingredients-text { position: absolute; top: 72px; left: 0; width: 100%; font-size: 12px; line-height: 16px; }
  .ratio { position: absolute; top: 130px; left: 0; width: 100%; font-weight: 700; font-size: 12px; }
  .flag { position: absolute; top: 184px; left: 72px; width: 56px; height: 30px; display: block; }
  .origin { position: absolute; top: 222px; left: 0; width: 100%; font-size: 14px; line-height: 18px; }
  .code-box {
    position: absolute; top: 283px; left: 9px; width: 183px; height: 78px;
    background: var(--box); color: var(--box-ink);
    display: flex; align-items: center; justify-content: center; font-size: 22px;
  }
</style>
</head>
<body>
<div class="canvas">
  <section class="label">
    <div class="col col-left">
      <h2 class="heading warnings-heading">Warnings:</h2>
      <p class="body-text warnings-text">Keep out of the reach of children. Always read the label before use. If swallowed consult a doctor if feeling unwell. In case of contact with eyes consult a doctor. Dispose of in a responsible manner. Store in a dark place at room temperature.</p>
      <div class="signs">
        <div class="sign sign-age">18+</div>
        <div class="sign sign-caution" role="img" aria-label="Caution sign">
          <svg width="34" height="30" viewBox="0 0 34 30" aria-hidden="true">
            <path d="M17 2 L32 28 L2 28 Z" fill="none" stroke="#1a1a1a" stroke-width="3" stroke-linejoin="round"/>
            <rect x="15.5" y="10" width="3" height="10" fill="#1a1a1a"/>
            <rect x="15.5" y="22" width="3" height="3" fill="#1a1a1a"/>
          </svg>
        </div>
      </div>
      <h2 class="heading address-heading">Address:</h2>
      <p class="body-text address-text">Lumora Liquids Ltd, Unit 4<br>Marsh Lane Trading Estate,<br>Leeds LS9 0AB, United Kingdom</p>
    </div>

    <div class="col col-centre">
      <div class="brand-mark">Lumora</div>
      <h1 class="range-name">Glitch</h1>
      <p class="product-type">Nicotine free eliquid</p>
      <div class="spec"><div class="spec-inner">Shortfill<br>100 ML | 0 Mg</div></div>
    </div>

    <div class="col col-right">
      <h2 class="heading ingredients-heading">Ingredients:</h2>
      <p class="body-text ingredients-text">Vegetable glycerin,<br>Propylene glycol,<br>Flavourings.</p>
      <p class="ratio">PG/VG ratio 70/30 %</p>
      <svg class="flag" viewBox="0 0 60 30" role="img" aria-label="United Kingdom flag">
        <rect width="60" height="30" fill="var(--flag-blue)"/>
        <path d="M0 0 L60 30 M60 0 L0 30" stroke="#fff" stroke-width="6"/>
        <path d="M0 0 L60 30 M60 0 L0 30" stroke="var(--flag-red)" stroke-width="2"/>
        <path d="M30 0 V30 M0 15 H60" stroke="#fff" stroke-width="10"/>
        <path d="M30 0 V30 M0 15 H60" stroke="var(--flag-red)" stroke-width="6"/>
      </svg>
      <p class="origin">Made in the United Kingdom</p>
      <div class="code-box">bar code</div>
    </div>
  </section>
</div>
</body>
</html>
```